New Business Card for Web Design/Internet Marketing Company

Looking for a great looking new business card. We are a 10 year old web design, internet marketing and website management company that works mostly with small businesses.

Our new card needs to better match the colors and style of our website, be bold, extremely usable and slightly edgy.

Target Market(s)

Small/Medium businesses that have websites

Industry/Entity Type

Internet

Requirements
Must have
• Front and back design, full color, rounded corners please

Must use the colors/style of our website (JPG provided)

INFO FOR CARDS (as readable as possible please)
Mark Lenner
President/CEO
mark@trelvanmedia.example
Phone: 520-381-7459
Toll Free: 866-381-7459
Address: 4315 W. Calloway Ave. Ste. 140, Tucson, AZ 85792

THINGS I WANT TO PROMOTE (if there is room):
1. Our Website - www.trelvanmedia.example

2. Social Media
Twitter: @trelvanmedia
Facebook: www.facebook.com/trelvanmedia

3. Our Services
Web Design
Internet Marketing
Website Management

```html
<!DOCTYPE html>
<html lang="en">
<head>
<meta charset="utf-8">
<title>Trelvan Media – Business Card</title>
<link rel="stylesheet" href="https://fonts.googleapis.com/css2?family=Fira+Sans+Condensed:wght@400;600&family=Open+Sans:wght@400;700&display=swap">
<style>
  :root{
    --bg:#eceef0;
    --blue:#1ea7dc;
    --ink:#141416;
    --ink-soft:#2a2c30;
    --slate:#3c3f44;
    --white:#ffffff;
    --muted:#d7dadd;
    --orange:#f07c1e;
  }
  *{margin:0;padding:0;box-sizing:border-box}
  html,body{width:1200px;height:900px;overflow:hidden;background:var(--bg)}
  body{position:relative;font-family:"Fira Sans Condensed",sans-serif}

  .card{position:absolute;left:320px;width:560px;height:320px;border-radius:22px;overflow:hidden;box-shadow:0 10px 28px rgba(0,0,0,.18)}
  .card--front{top:100px;background:var(--blue)}
  .card--back{top:480px;background:var(--ink)}

  /* front */
  .edge-tabs{position:absolute;left:0;top:38px;width:22px}
  .edge-tabs span{display:block;height:44px;margin-bottom:6px;background:var(--slate);border-radius:0 4px 4px 0}
  .person{position:absolute;left:52px;top:40px}
  .person__name{font-family:"Open Sans",sans-serif;font-size:34px;font-weight:400;line-height:1;color:var(--white)}
  .person__first{color:var(--ink-soft);text-transform:uppercase}
  .person__title{font-size:13px;color:var(--ink-soft);margin-top:4px}
  .contact{position:absolute;left:42px;top:118px;list-style:none}
  .contact li{display:flex;align-items:center;gap:10px;height:30px;font-size:15px;color:var(--white)}
  .contact svg{width:16px;height:16px;flex:none}
  .contact .toll{background:var(--ink);border-radius:8px;padding:0 12px 0 6px;height:32px;font-size:19px;margin:2px 0}
  .contact .small{font-size:14px}
  .brand-band{position:absolute;left:400px;top:0;width:84px;height:100%;background:var(--ink)}
  .brand-band__text{position:absolute;left:50%;top:50%;transform:translate(-50%,-50%) rotate(90deg);white-space:nowrap;text-align:right}
  .brand-band__name{display:block;font-family:"Open Sans",sans-serif;font-weight:700;font-size:28px;line-height:1.1;color:var(--blue)}
  .brand-band__tag{display:block;font-size:11px;color:var(--slate);letter-spacing:.3px}

  /* back */
  .back-curves{position:absolute;inset:0;width:100%;height:100%}
  .back-content{position:absolute;inset:0;display:flex;flex-direction:column;align-items:center;justify-content:center;gap:12px}
  .brand-lockup{display:flex;flex-direction:column;align-items:flex-end}
  .brand-mark{display:flex;align-items:center;gap:12px;font-family:"Open Sans",sans-serif;font-weight:700;font-size:44px;line-height:1.1;color:var(--blue)}
  .brand-mark__dot{width:26px;height:26px;border-radius:50%;background:var(--orange)}
  .brand-tag{font-size:13px;color:var(--slate);letter-spacing:.3px}
  .services{background:var(--blue);color:var(--white);font-size:14px;padding:3px 12px;border-radius:3px}
  .social{display:flex;gap:22px;font-size:13px;color:var(--muted)}
  .social__item{display:flex;align-items:center;gap:6px}
  .social__item i{width:12px;height:12px;border-radius:50%;background:var(--blue);display:block}
  .social__pill{background:var(--blue);color:var(--white);padding:1px 10px;border-radius:10px}
</style>
</head>
<body>

<section class="card card--front" aria-label="Business card front">
  <div class="edge-tabs"><span></span><span></span><span></span></div>

  <div class="person">
    <h1 class="person__name"><span class="person__first">Mark</span> Lenner</h1>
    <p class="person__title">President/CEO</p>
  </div>

  <ul class="contact">
    <li class="small">
      <svg viewBox="0 0 16 16"><path d="M8 1a5 5 0 0 0-5 5c0 4 5 9 5 9s5-5 5-9a5 5 0 0 0-5-5zm0 7a2 2 0 1 1 0-4 2 2 0 0 1 0 4z" fill="#fff"/></svg>
      4315 W. Calloway Ave. Ste. 140, Tucson, AZ 85792
    </li>
    <li>
      <svg viewBox="0 0 16 16"><path d="M4 1l3 3-2 2c1 2 3 4 5 5l2-2 3 3-2 3C7 15 1 9 1 3z" fill="#fff"/></svg>
      520-381-7459
    </li>
    <li class="toll">
      <svg viewBox="0 0 16 16"><path d="M4 1l3 3-2 2c1 2 3 4 5 5l2-2 3 3-2 3C7 15 1 9 1 3z" fill="#fff"/></svg>
      866-381-7459 (Toll Free)
    </li>
    <li class="small">
      <svg viewBox="0 0 16 16"><rect x="1" y="3" width="14" height="10" rx="1" fill="#fff"/><path d="M1 4l7 5 7-5" stroke="#1ea7dc" stroke-width="1.5" fill="none"/></svg>
      mark@trelvanmedia.example
    </li>
    <li class="small">
      <svg viewBox="0 0 16 16"><circle cx="8" cy="8" r="6.5" fill="none" stroke="#fff" stroke-width="1.5"/><path d="M1.5 8h13M8 1.5c-3 3-3 10 0 13M8 1.5c3 3 3 10 0 13" stroke="#fff" stroke-width="1.2" fill="none"/></svg>
      www.trelvanmedia.example
    </li>
  </ul>

  <div class="brand-band">
    <div class="brand-band__text">
      <span class="brand-band__name">Trelvan Media</span>
      <span class="brand-band__tag">Websites that work</span>
    </div>
  </div>
</section>

<section class="card card--back" aria-label="Business card back">
  <svg class="back-curves" viewBox="0 0 560 320" preserveAspectRatio="none" aria-hidden="true">
    <path d="M0 0H150C90 10 40 50 0 120Z" fill="#1ea7dc"/>
    <path d="M560 320H410C470 310 520 270 560 200Z" fill="#1ea7dc"/>
  </svg>
  <div class="back-content">
    <div class="brand-lockup">
      <div class="brand-mark"><span class="brand-mark__dot"></span>Trelvan Media</div>
      <span class="brand-tag">Websites that work</span>
    </div>
    <p class="services">Web Design | Internet Marketing | Website Management</p>
    <div class="social">
      <span class="social__item"><i></i>www.friendsnet.example/trelvanmedia</span>
      <span class="social__item"><i></i><span class="social__pill">@trelvanmedia</span></span>
    </div>
  </div>
</section>

</body>
</html>
```